Web design project for exciting Australian start-up

Background
We are looking for a creative and talented web design artist to work alongside our market leading web developer.
• You will be required to create a modern and clean design theme for our website, incorporating selected rustic colour scheme elements for our exciting Australian start-up to operate within the coffee industry.
reoccurring work to be expected to flow to the successful designer.
Requirements
• c. 5 - 10 page website
• Landing page
• Log in/ out
• 404 template
• Typography is emphasised
• Please use either a) typemarrow.com, b) free web fonts, c) brindle fonts
• All design elements in vector format
• Preferably with icons for each header title(i.e. about us, how it works etc) but designer have free reign over how the site looks, so might not be applicable
• All pages to be responsive
• Down to eSlab resolution

High level visual design brief attached - additional pages to be worked from base design.

Design inspiration
• We would like to use design elements from the following sources:
http://www.zandrix.com/halcyon/ (Functionality)
Colour scheme refer to logo and complementary style guide

```html
<!DOCTYPE html>
<html lang="en">
<head>
<meta charset="utf-8">
<title>Roastline – Market Place</title>
<link rel="stylesheet" href="https://fonts.googleapis.com/css2?family=Open+Sans:wght@400;600;700&family=Arimo:wght@400;700&display=swap">
<style>
:root{
  --orange:#f68b39;
  --ink:#333333;
  --text:#4a4a4a;
  --white:#ffffff;
  --footer:#3d3e40;
  --footer-box:#56575a;
  --bar:#ebebeb;
  --rule:#d6d6d6;
  --panel:rgba(92,72,58,.72);
  --wood-light:#8a6b58;
  --wood-mid:#6a4a38;
  --wood-dark:#3e2619;
}
*{margin:0;padding:0;box-sizing:border-box}
html,body{width:1200px;height:1187px;overflow:hidden;background:var(--white)}
body{position:relative;font-family:"Open Sans",Arial,sans-serif;color:var(--text)}
a{color:inherit;text-decoration:none}

/* header */
.site-header{position:absolute;left:0;top:0;width:1200px;height:108px;background:var(--white)}
.brand{position:absolute;left:88px;top:38px;display:flex;align-items:center;gap:10px;font-family:"Open Sans",sans-serif;font-weight:700;font-size:26px;letter-spacing:1px;color:var(--ink)}
.brand-dot{width:26px;height:26px;border-radius:50%;background:var(--orange)}
.main-nav{position:absolute;top:0;left:0;font-family:Arimo,Arial,sans-serif;font-size:16px;color:var(--ink)}
.main-nav a{position:absolute;top:48px;white-space:nowrap}
.main-nav .is-active{top:0;height:73px;width:102px;background:var(--orange);color:var(--white);text-align:center;padding-top:48px}
.login-btn{position:absolute;left:1018px;top:44px;width:73px;height:28px;border-radius:4px;background:var(--orange);color:var(--white);font-family:Arimo,Arial,sans-serif;font-size:16px;text-align:center;line-height:28px}

/* hero */
.hero{position:absolute;left:0;top:108px;width:1200px;height:539px}
.hero-photo{position:absolute;inset:0;background:linear-gradient(180deg,var(--wood-light) 0%,var(--wood-mid) 60%,var(--wood-dark) 100%)}
.hero-title{position:absolute;left:87px;top:56px;font-weight:700;font-size:52px;color:var(--white);letter-spacing:.5px;text-shadow:0 2px 4px rgba(0,0,0,.35)}
.btn{display:block;background:var(--orange);color:var(--white);font-weight:600;text-transform:uppercase;text-align:center}
.start-btn{position:absolute;left:94px;top:140px;width:202px;height:45px;font-size:20px;line-height:45px}
.select-panel{position:absolute;left:579px;top:29px;width:492px;height:479px;background:var(--panel)}
.select-title{position:absolute;left:50px;top:11px;font-weight:700;font-size:19px;color:var(--orange)}
.select-row{position:absolute;left:49px;width:420px;height:27px}
.select-row label{position:absolute;left:0;top:3px;font-size:14.5px;color:var(--white)}
.select-box{position:absolute;left:147px;top:0;width:245px;height:27px;background:var(--white);border:1px solid #ddd}
.select-box svg{position:absolute;right:10px;top:9px}
.launch-btn{position:absolute;left:724px;top:445px;width:202px;height:47px;font-size:20px;line-height:47px}

/* content */
.section-title{position:absolute;left:88px;top:684px;font-weight:700;font-size:19px;color:var(--orange)}
.section-rule{position:absolute;left:88px;top:726px;width:1024px;height:1px;background:var(--rule)}
.intro-photo{position:absolute;left:88px;top:746px;width:145px;height:145px;border-radius:50%;background:linear-gradient(160deg,#e8a23a 0%,#a8602a 45%,#3a2318 100%);border:2px solid var(--orange)}
.intro-text{position:absolute;left:259px;top:751px;width:853px;font-size:13px;line-height:21.8px;color:var(--text);text-align:justify}

/* footer */
.footer-line{position:absolute;left:0;top:939px;width:1200px;height:8px;background:var(--orange)}
.site-footer{position:absolute;left:0;top:947px;width:1200px;height:198px;background:var(--footer);color:var(--white)}
.footer-col{position:absolute;top:18px}
.footer-col h3{font-weight:600;font-size:17.5px;color:var(--orange);margin-bottom:22px}
.footer-list{list-style:none;font-size:13.3px}
.footer-list li{position:relative;padding-left:24px;height:24px;line-height:20px}
.footer-list li::before{content:"";position:absolute;left:0;top:5px;border-left:7px solid var(--white);border-top:5px solid transparent;border-bottom:5px solid transparent}
.social-grid{display:grid;grid-template-columns:120px 100px;row-gap:14px;font-size:13.3px}
.social-item{display:flex;align-items:center;gap:12px}
.social-mark{width:24px;height:24px;background:#7d8085;border-radius:3px}
.contact-box{position:absolute;left:837px;width:276px;height:32px;background:var(--footer-box);border-radius:3px;font-family:Arimo,Arial,sans-serif;font-size:13px;line-height:32px;padding-left:16px}
.copyright{position:absolute;left:0;top:1145px;width:1200px;height:42px;background:var(--bar);font-family:Arimo,Arial,sans-serif;font-size:11.5px;color:var(--ink);text-align:center;line-height:42px}
</style>
</head>
<body>

<header class="site-header">
  <div class="brand"><span class="brand-dot"></span>ROASTLINE</div>
  <nav class="main-nav">
    <a href="#" style="left:494px">Home</a>
    <a href="#" style="left:576px">About Us</a>
    <a href="#" style="left:682px">Who we are</a>
    <a href="#" class="is-active" style="left:790px">Market Place</a>
    <a href="#" style="left:920px">Contact Us</a>
  </nav>
  <a href="#" class="login-btn">Login</a>
</header>

<section class="hero">
  <div class="hero-photo" role="img" aria-label="Photo: white coffee cup on saucer beside roasted coffee beans on a wooden table"></div>
  <h1 class="hero-title">MARKET PLACE</h1>
  <a href="#" class="btn start-btn">Start Tender &nbsp;›</a>

  <form class="select-panel">
    <h2 class="select-title">SELECT</h2>
    <div class="select-row" style="top:68px"><label>Tender type</label><div class="select-box"><svg width="10" height="8"><path d="M0 0h10L5 8z" fill="#999"/></svg></div></div>
    <div class="select-row" style="top:116px"><label>Quantity (kg)</label><div class="select-box"><svg width="10" height="8"><path d="M0 0h10L5 8z" fill="#999"/></svg></div></div>
    <div class="select-row" style="top:164px"><label>Machinery</label><div class="select-box"><svg width="10" height="8"><path d="M0 0h10L5 8z" fill="#999"/></svg></div></div>
    <div class="select-row" style="top:212px"><label>Wholesaler</label><div class="select-box"><svg width="10" height="8"><path d="M0 0h10L5 8z" fill="#999"/></svg></div></div>
    <div class="select-row" style="top:261px"><label>Barista training</label><div class="select-box"><svg width="10" height="8"><path d="M0 0h10L5 8z" fill="#999"/></svg></div></div>
    <div class="select-row" style="top:308px"><label>Accessories</label><div class="select-box"><svg width="10" height="8"><path d="M0 0h10L5 8z" fill="#999"/></svg></div></div>
    <div class="select-row" style="top:356px"><label>Promotion support</label><div class="select-box"><svg width="10" height="8"><path d="M0 0h10L5 8z" fill="#999"/></svg></div></div>
  </form>
  <a href="#" class="btn launch-btn">Launch Tender</a>
</section>

<main>
  <h2 class="section-title">MARKET PLACE</h2>
  <div class="section-rule"></div>
  <div class="intro-photo" role="img" aria-label="Photo: steaming cup of coffee on a bed of coffee beans"></div>
  <p class="intro-text">Vitae dolores sit et. Vis ex elit reque commune, suas atqui habemus ne mea, per esse errem senserit ei. Vim ne habeo libris reformidans. Vivendum repudiandae ullamcorper ad per, vis dolore tibique ea. Decore partem no cum. Id vis nobis invidunt, ei fugit novum definitiones mei.Vitae dolores sit et. Vis ex elit reque commune, suas atqui habemus ne mea, per esse errem senserit ei. Vim ne habeo libris reformidans. Vivendum repudiandae ullamcorper ad per, vis dolore tibique ea. Decore partem no cum. Id vis nobis invidunt, ei fugit novum definitiones mei.Vitae dolores sit et. Vis ex elit reque commune, suas atqui habemus ne mea, per esse errem senserit ei. Vim ne habeo libris reformidans. Vivendum repudiandae ullamcorper ad per, vis dolore tibique ea. Decore partem no cum. Id vis nobis invidunt.</p>
</main>

<div class="footer-line"></div>
<footer class="site-footer">
  <div class="footer-col" style="left:89px">
    <h3>Helpful Info</h3>
    <ul class="footer-list"><li>About us</li><li>Media enquiries</li><li>Terms &amp; conditions</li><li>Privacy policy</li></ul>
  </div>
  <div class="footer-col" style="left:333px">
    <h3>Who We Are</h3>
    <ul class="footer-list"><li>How it works</li><li>FAQ</li><li>Contact us</li></ul>
  </div>
  <div class="footer-col" style="left:563px">
    <h3>Join Us On</h3>
    <div class="social-grid">
      <span class="social-item"><span class="social-mark"></span>Friendloop</span>
      <span class="social-item"><span class="social-mark"></span>Worknest</span>
      <span class="social-item"><span class="social-mark"></span>Chirpwell</span>
      <span class="social-item"><span class="social-mark"></span>Clipstream</span>
    </div>
  </div>
  <div class="footer-col" style="left:837px"><h3>Contact Us</h3></div>
  <div class="contact-box" style="top:65px">Company Adress, Australia</div>
  <div class="contact-box" style="top:103px">Phone: +1 (555) 010 2847</div>
  <div class="contact-box" style="top:141px">Email: info@roastline.com</div>
</footer>
<div class="copyright">© copy right 2014 Roastline | All Rights Reserved</div>

</body>
</html>
```